Screen-Design für Website (Recruiting Agency)
Ich bin wirklich äußerst zufrieden mit der Arbeit und der Zusammenarbeit: tesmaruplin ist auf jeden meiner Wünsche eingegangen und hat mir auch geduldig die verschiedenesten Varianten erarbeitet, wenn ich mir mal die Vorstellungskraft fehlte. Die 5 Sterne sind mehr als verdient. __ I am really extremely satisfied with the work and the cooperation: tesmaruplin has responded to every one of my wishes and has also patiently worked out the most varied of variants for me when I lacked the imagination. The 5 stars are more than deserved.
Zielgruppe
An english version of the briefing can be found at the end
Briefing:
Kurzbeschreibung des Projektes
ich möchte ich mit einer Agentur für Recruiting zum Januar 2021 selbstständig machen und benötige für meine Website noch ein grundlegendes Screen-Design und Bilder, Kollagen und/oder Illustrationen für die verschiednen Textblöcke für zunächst vier Seiten , die die Inhalte transportieren sollen und 'Lust auf das Lesen der Texte' machen.
Ich lasse mich auch von euch Profis gerne beraten, wenn bspw. Überschriften fehlen, Call-to-Action-Elemente (bspw. Kontaktformulare) anders positioniert oder der Footer andere Inhalte enthalten sollte.
Ich benötige
Frühe Entwicklungs-/Konzeptphase als Entscheidungsgrundlage
Ein Screendesign (als PDF, JPG oder via pv.morlint.com-Webansicht) für eine der vier Seiten und die Entwicklung der dazugehörigen Bildelemente.
Am Ende des Prozesses:
- das Screendesign (als PDF, JPG oder via pv.morlint.com-Webansicht)
- Entwicklung der Bildelemente (Bilder, Kollagen oder Ilustrationen) für die verschiedenen Absätze aller vier Seiten
- webfähige Bild-Formate der einzelenen Elemente (Header, Hintergründe, Bilder) fü ride Wordpress-Umsetzung des Designs
Nachtrag 16.11.2020:
Da bereits mehrfach nachgefragt wurde, konkretisiere ich noch einmal den Ablauf (entschuldigt bitte die Verwirrung):
Ich möchte den Aufwand in der Konzeptionsphase für die teilnehmenden Designer so gering wie möglich halten, daher:
Erwarte ichzunächst ein Screendesign für eine einzige Seite . Auf dieser Basis möchte ich eine Entscheidung treffen können. Dieses Screendesign beinhaltet den grundlegenden Aufbau und das grundlegende Design der miren-Seite, die Elemente, Bilder und/oder Illustrationen, die zu dieser konkreten Seite gehören. Eventuell frage ich euch, ob ihr noch das eine oder andere an diesem Entwurf anpassen oder konkretieseren könntet.
Aufgabenstellung
An english version of the project description and goals can be found at the end
Projektbeschreibung und Ziele
Projekthintergrund
Der Vertrieb soll im Januar 2021 starten und dazu benötige ich eine professionelle Website, die die vorgenannten Zielgruppen „emotional“ zum Stöbern einlädt und neugierig auf mehr miren macht. Vertrauen schafft.
Den Dummy der Website (ein Wordpress-Theme (Varlow: https://bramuth.at/themes/varlow-overview/) mit den bereits finalen Texten finden Sie unter https://mi-kobalt.de.
Hier ist nichts „designt“, sondern dient erst einmal lediglich dazu, das Projekt und die Texte der Seiten zu transportieren und festzulegen. Also bitte nicht an den Anordnungen der Textblöcke, Farbwahl oder Schriftgrößen stören - das ist wirklich nur ein Dummy.
Konkret geht es bei diesem Auftrag um folgende vier Seiten:
_Home
_Stellenanzeigen Recruiting
_Performance Recrutiing
_Recruitment Insights
Alle weiteren Seiten (über uns, Blog, Impressum, usw.) sind exemplarisch zwar schon angelegt, werden aber zu einem späteren Zeitpunkt angegangen.
Ziele
An der Unterseite https://mi-kobalt.de/recruitment_insights/ möchte ich gerne dokumentieren, was ich genau benötige.
Die einzelnen Textblöcke der vier Unterseiten sollen durch Bilder, Collagen und/oder Illustrationen unterstützt werden, die Seite „auflockern“ und dem User helfen, schneller den jeweiligen Inhalt und seinen Vorteil zu erfassen (in der Hoffnung, dass er dann auch die dazugehörigen Texte liest).
Inspirierend fand ich bspw. Seiten wie,
https://www.quenvik.com/insights/
https://www.holdenfeld.com/recruiting-software/plexposts/,
https://www.bavorent.com/solutions/programmatic-job-advertising
https://pelzorix.com/
Wichtige Icons bzw. Logos, die mit der Branche und den Schaltkanälen in Verbindung stehen, habe ich Ihnen als PPT-Datei angehängt, falls Sie diese in einem Entwurf ve..

```html
<!DOCTYPE html>
<html lang="de">
<head>
<meta charset="utf-8">
<title>miren advisory – Recruiting</title>
<link href="https://fonts.googleapis.com/css2?family=Source+Sans+3:wght@300;400;600;700&display=swap" rel="stylesheet">
<style>
:root{
  --ink-dark:#230b5a;
  --violet:#8a1fa8;
  --violet-deep:#4b1f8f;
  --heading:#4a1a86;
  --magenta:#8e1ea6;
  --text:#555;
  --card-bg:#f6f6f6;
  --white:#fff;
}
*{margin:0;padding:0;box-sizing:border-box}
html,body{width:1200px;height:2418px;overflow:hidden}
body{font-family:"Source Sans 3",sans-serif;color:var(--text);background:var(--white);position:relative}
.abs{position:absolute}
.topbar{position:absolute;top:0;left:0;width:1200px;height:40px;background:var(--ink-dark);color:#fff;font-size:13px;font-weight:600}
.topbar .mail{left:150px;top:12px;display:flex;gap:10px;align-items:center}
.topbar .phone{right:150px;top:10px;font-size:15px;display:flex;gap:8px;align-items:center}
.nav{position:absolute;top:40px;left:0;width:1200px;height:72px;background:var(--violet);color:#fff}
.brand{left:150px;top:18px;font-size:30px;font-weight:400;letter-spacing:.3px}
.brand b{font-weight:700}
.menu{right:150px;top:27px;display:flex;gap:34px;font-size:14px;font-weight:600}
.hero{position:absolute;top:112px;left:0;width:1200px;height:408px;background:linear-gradient(90deg,#4f2a8e,#5a2f9a 60%,#6a3aa6);overflow:hidden}
.hero-photo{position:absolute;inset:0}
.hero h1{position:absolute;left:148px;top:122px;color:#fff;font-size:40px;line-height:42px;font-weight:700}
.hero h1 span{display:block;font-weight:400}
.btn{position:absolute;height:43px;border-radius:3px;color:#fff;font-weight:600;font-size:16px;display:flex;align-items:center;justify-content:center}
.btn-start{left:150px;top:232px;width:130px;background:var(--violet)}
.btn-more{left:298px;top:232px;width:131px;background:var(--ink-dark)}
.intro-title{left:551px;top:606px;font-size:27px;font-weight:600;color:var(--heading)}
.intro-text{left:551px;top:654px;width:500px;font-size:14.5px;line-height:22.5px;font-weight:300;color:#666}
.intro-text b{font-weight:400;color:#444}
.section-title{width:1200px;text-align:center;font-size:27px;font-weight:600;color:var(--heading)}
.section-sub{width:1200px;text-align:center;font-size:13px;font-weight:300;color:#555}
.card{position:absolute;top:977px;width:291px;height:496px;background:var(--card-bg)}
.card .photo{height:215px}
.card .tag{height:29px;background:var(--violet);color:#fff;font-size:15px;font-weight:600;padding:5px 0 0 29px}
.card h3{font-size:20px;line-height:23px;font-weight:600;color:var(--magenta);margin:18px 10px 0 29px;white-space:nowrap}
.card p{font-size:12.5px;line-height:19.5px;font-weight:300;color:#444;margin:14px 28px 0 31px}
.arrow{position:absolute;top:1184px;width:42px;height:42px;border-radius:50%;background:var(--ink-dark);display:flex;align-items:center;justify-content:center}
.cta{position:absolute;top:1518px;left:0;width:1200px;height:410px;overflow:hidden}
.cta h2{position:absolute;left:150px;top:48px;font-size:25px;line-height:27px;font-weight:600;color:var(--ink-dark);white-space:nowrap}
.cta .note{left:150px;top:163px;font-size:12.5px;color:#333}
.cta .call{left:150px;top:195px;font-size:25px;font-weight:300;color:#333}
.cta .num{left:150px;top:223px;font-size:37px;font-weight:700;color:var(--magenta)}
.cta .form-hint{left:150px;top:277px;font-size:14px;font-weight:600;color:var(--ink-dark)}
.field{position:absolute;left:697px;width:313px;background:#fff;border-radius:3px;font-size:16px;color:#333;padding:10px 16px}
.send{position:absolute;left:697px;top:298px;width:313px;height:44px;background:var(--violet);border-radius:3px;color:#fff;font-size:18px;font-weight:600;display:flex;align-items:center;justify-content:center}
.partners h2{position:absolute;font-size:23px;font-weight:600;color:var(--ink-dark)}
.logo-box{position:absolute;top:2022px;width:145px;height:70px;background:#f4f4f6;border:1px solid #e7e7ea;display:flex;align-items:center;justify-content:center;gap:7px;font-size:20px;font-weight:600;color:#3b5fd0}
.logo-box i{width:10px;height:10px;border-radius:50%;background:currentColor;display:block}
.partner-text{position:absolute;top:2026px;width:252px;font-size:13px;line-height:19.5px;font-weight:300;color:#555}
.dots{position:absolute;top:2116px;display:flex;gap:7px}
.dots span{width:8px;height:8px;border-radius:50%;background:var(--ink-dark)}
.dots span:first-child{background:var(--violet)}
.divider{position:absolute;left:600px;top:1943px;width:1px;height:192px;background:#ccc}
.footer{position:absolute;top:2148px;left:0;width:1200px;height:270px;background:linear-gradient(180deg,#2e0e63,#4a1680 60%,#6a1d98);color:#fff}
.footer h4{position:absolute;top:38px;font-size:16px;font-weight:400}
.footer ul{position:absolute;top:76px;list-style:none;font-size:13px;line-height:22.5px}
.footer .addr{position:absolute;top:76px;font-size:13px;line-height:16px}
.social{position:absolute;top:145px;left:670px;display:flex;gap:18px;align-items:center;font-size:12px;font-weight:600}
.footer .rule{position:absolute;left:150px;top:236px;width:900px;height:1px;background:rgba(255,255,255,.2)}
.copy{position:absolute;top:244px;width:1200px;text-align:center;font-size:13px}
</style>
</head>
<body>

<header class="topbar">
  <div class="abs mail">
    <svg width="18" height="12" viewBox="0 0 18 12"><rect x=".5" y=".5" width="17" height="11" fill="none" stroke="#fff"/><path d="M1 1l8 6 8-6" fill="none" stroke="#fff"/></svg>
    kontakt@miren-advisory.de
  </div>
  <div class="abs phone">
    <svg width="15" height="15" viewBox="0 0 24 24"><path d="M6.6 10.8a15 15 0 006.6 6.6l2.2-2.2c.3-.3.7-.4 1-.2 1.1.4 2.3.6 3.6.6.6 0 1 .4 1 1V20c0 .6-.4 1-1 1A17 17 0 013 4c0-.6.4-1 1-1h3.5c.6 0 1 .4 1 1 0 1.3.2 2.5.6 3.6.1.3 0 .7-.2 1z" fill="#fff"/></svg>
    +49 6171 482 307
  </div>
</header>

<nav class="nav">
  <div class="abs brand"><b>miren</b> advisory</div>
  <div class="abs menu">
    <span>Home</span><span>Stellenanzeigen Recruiting</span><span>Performance Recruiting</span><span>Recruitment Insights</span><span>kontakt</span>
  </div>
</nav>

<section class="hero">
  <svg class="hero-photo" width="1200" height="408" role="img" aria-label="Foto: zwei Geschäftsmänner geben sich im hellen Büro die Hand">
    <defs><linearGradient id="heroPhoto" x1="0" y1="0" x2="1" y2="1"><stop offset="0" stop-color="#c9d6e4"/><stop offset=".5" stop-color="#9fb0c4"/><stop offset="1" stop-color="#4a5469"/></linearGradient></defs>
    <polygon points="808,0 1200,0 1200,408 493,408" fill="url(#heroPhoto)"/>
  </svg>
  <h1>Die besten Talente gewinnen.<span>Stellen besetzen.</span></h1>
  <div class="btn btn-start">Jetzt Starten</div>
  <div class="btn btn-more">Mehr Erfahren</div>
</section>

<section class="intro">
  <svg class="abs" style="left:140px;top:560px" width="400" height="290" viewBox="0 0 400 290" role="img" aria-label="Foto von oben: Team im Gespräch im Büro, in organischer Form">
    <defs><linearGradient id="blob" x1="0" y1="0" x2="1" y2="1"><stop offset="0" stop-color="#8a96a8"/><stop offset=".5" stop-color="#c3cdd8"/><stop offset="1" stop-color="#e2e7ee"/></linearGradient></defs>
    <path d="M30 60C60 30 150 40 200 36c60-4 120-20 160 6 30 20 18 80 12 130-8 60-60 70-130 70-60 0-110 40-170 0C20 210 0 150 6 110 10 90 14 74 30 60z" fill="url(#blob)"/>
    <circle cx="176" cy="48" r="17" fill="#2a0a5e"/>
    <circle cx="260" cy="33" r="28" fill="#8a1fa8"/>
    <circle cx="373" cy="156" r="9" fill="#6a3ab0"/>
  </svg>
  <div class="abs intro-title">Nice heading goes here</div>
  <p class="abs intro-text"><b>Online-Recruiting kann frustrierend sein:</b> Entweder erhält man keine oder viel zu viele unpassende <b>Bewerbungen. Und doch gibt es sie:</b> Die Talente, die perfekt zu Ihren offenen Positionen passen. Wir helfen Ihnen, die besten Talente zu erreichen.</p>
</section>

<section class="services">
  <div class="abs section-title" style="top:893px">Was wir für sie tun</div>
  <div class="abs section-sub" style="top:936px">Wenn Erfahrung und Leidenschaft auf Technologie treffen, dann bekommen Sie die Kandidaten, die Sie brauchen.</div>

  <div class="arrow" style="left:81px"><svg width="14" height="14" viewBox="0 0 14 14"><path d="M9 2L4 7l5 5" stroke="#fff" stroke-width="2" fill="none"/></svg></div>
  <div class="arrow" style="left:1073px"><svg width="14" height="14" viewBox="0 0 14 14"><path d="M5 2l5 5-5 5" stroke="#fff" stroke-width="2" fill="none"/></svg></div>

  <article class="card" style="left:150px">
    <div class="photo" role="img" aria-label="Foto: Team in einer Besprechung am Konferenztisch" style="background:linear-gradient(135deg,#e4e6ea,#b9bdc5 60%,#8d929c)"></div>
    <div class="tag">Stellenanzeigen Recruiting</div>
    <h3>„Post &amp; Pray“ war gestern<br>schon out</h3>
    <p>Während Ihre Wettbewerber noch „beten“, erreichen wir bereits die relevanten Kandidaten, die wirklich zu Ihren offenen Stellen passen: Zielgruppenoptimierte Stellenanzeigen auf den nachweisbar relevanten Jobbörsen, Nischen-Stellenbörsen, Netzwerken oder Special Interest-Portalen.</p>
  </article>
  <article class="card" style="left:455px">
    <div class="photo" role="img" aria-label="Foto: Tablet mit Diagrammen und Auswertungen" style="background:linear-gradient(135deg,#dfe6ee,#7fb3cf 55%,#2f6f9a)"></div>
    <div class="tag" style="padding-left:22px">Recruiting Insights</div>
    <h3 style="margin-left:22px">Cleverer als Ihr Wettbewerb</h3>
    <p style="margin-left:23px;margin-right:16px">Seien auch Sie cleverer als Ihre Wettbewerber: Unsere Reruitment Insights informieren Sie über Traffic-Trends, Arbeitsmarkt und Wettbewerb. So beurteilen Sie die Empfehlungen transparent – bvor Sie uns beauftragen. Kostenlos und unverbindlich.<br><br>Damit Sie sich schneller und effizienter die besseren Talente sichern.</p>
  </article>
  <article class="card" style="left:760px">
    <div class="photo" role="img" aria-label="Foto: lächelnde Frau im hellen Büro" style="background:linear-gradient(135deg,#cfdde0,#9fb9bc 55%,#6f8d94)"></div>
    <div class="tag" style="padding-left:24px">Performance Recruiting</div>
    <h3 style="margin-left:24px">Die eigentlich unerreichbaren<br>Talente erreichen</h3>
    <p style="margin-left:26px;margin-right:34px">miren verwandelt Ihre Stellenanzeigen in sich selbst-optimierende Anzeigenkampagnen. Dank unsere KI-gestützten Recruiting Ads und Stellenanzeigen erreichen Sie auch passive Kandidaten. Das gesamte Internet als Jobbörse.: Bis zu 10-mal mehr Kandidaten. Hocheffizient.</p>
  </article>
</section>

<section class="cta">
  <div class="abs" role="img" aria-label="Unscharfes Foto: heller Büroraum im Hintergrund" style="inset:0;background:linear-gradient(90deg,#c9b79a,#e6ddd0 40%,#d9cfc2)"></div>
  <svg class="abs" style="left:0;top:0" width="1200" height="410" role="img" aria-label="Unscharfes Foto: Menschen im Büro, violett eingefärbt">
    <defs><linearGradient id="ctaPurple" x1="0" y1="0" x2="1" y2="0"><stop offset="0" stop-color="#4d2a8c"/><stop offset="1" stop-color="#3a1f75"/></linearGradient></defs>
    <polygon points="678,0 1200,0 1200,410 428,410" fill="url(#ctaPurple)"/>
  </svg>
  <h2>Sie wollen miren in Aktion erleben?<br>Mehr, relevante Bewerbungen erhalten?<br>Stellen besetzen? Mit den besten<br>Talenten?</h2>
  <div class="abs note">Wir sind für Sie da und freuen uns auf Ihre Herausforderung.</div>
  <div class="abs call">Rufen Sie uns an unter</div>
  <div class="abs num">06171 – 482 307</div>
  <div class="abs form-hint">oder kontaktieren Sie uns per Formular:</div>
  <div class="field" style="top:73px;height:45px">Name</div>
  <div class="field" style="top:132px;height:45px">E-Mail</div>
  <div class="field" style="top:189px;height:98px;padding-top:14px">Ihre Nachricht an miren*</div>
  <div class="send">Jetzt miren Kontaktieren</div>
</section>

<section class="partners">
  <h2 style="left:152px;top:1963px">Performance Recruiting. Social Media.</h2>
  <h2 style="left:640px;top:1963px">Jobbörsen. Nischenjobbörsen.</h2>
  <div class="logo-box" style="left:150px"><i></i>Jobvanta</div>
  <div class="partner-text" style="left:315px">Lorem ipsum dolor sit amet, consectetur adipisci elit, sed eiusmod tempor incidunt ut labore et dolore magna aliqua.</div>
  <div class="logo-box" style="left:640px;color:#2a3a8c"><i></i>Kareon</div>
  <div class="partner-text" style="left:805px">Lorem ipsum dolor sit amet, consectetur adipisci elit, sed eiusmod tempor incidunt ut labore et dolore magna aliqua.</div>
  <div class="dots" style="left:340px"><span></span><span></span><span></span><span></span><span></span></div>
  <div class="dots" style="left:831px"><span></span><span></span><span></span><span></span><span></span></div>
  <div class="divider"></div>
</section>

<footer class="footer">
  <div class="abs" role="img" aria-label="Dezente Weltkarte als Hintergrund" style="left:560px;top:20px;width:600px;height:210px;background:radial-gradient(ellipse at center,rgba(40,10,90,.35),rgba(40,10,90,0) 70%)"></div>
  <h4 style="left:151px">Wichtige Links</h4>
  <ul style="left:151px"><li>Recruitment Insights</li><li>Performance Recruiting</li><li>Stellenanzeigen Recruiting</li><li>Blog</li></ul>
  <ul style="left:379px"><li>Datenschutz</li><li>Impressum</li><li>über uns</li><li>Kontakt</li></ul>
  <h4 style="left:669px">KONTAKT</h4>
  <div class="addr" style="left:669px">miren advisory UG<br>Lindenhofweg 7<br>65719 Hofheim am Taunus</div>
  <div class="addr" style="left:839px">Telefon +49 6171 482 307<br>E-Mail kontakt@miren-advisory.de</div>
  <div class="social">
    <span>Xelvo</span><span>Linqo</span>
    <svg width="14" height="10" viewBox="0 0 14 10"><rect width="14" height="10" rx="1" fill="#fff"/><path d="M1 1l6 4 6-4" stroke="#4a1680" fill="none"/></svg>
  </div>
  <div class="rule"></div>
  <div class="copy">Copyright © 2020. All rights reserved.</div>
</footer>

</body>
</html>
```